Corvena Hotel, city center modern minimal hotel operating all year round, on Rhodes island Greece

city, modern ,all year operating hotel

Target Market(s)

tourists, business agents

Industry/Entity Type

tourism

Number of Pages Required

2 page

Requirements
Must have
• room type photos and descriptions, amenities individual listing (graphic), comments sections, map driving location details
Nice to have
• gallery section, modern and minimal design, amenities section, individual room type descriptions, photos and facilities

```html
<!DOCTYPE html>
<html lang="en">
<head>
<meta charset="utf-8">
<title>Corvena Hotel</title>
<link href="https://fonts.googleapis.com/css2?family=Marcellus&family=Barlow:wght@400;500;600;700&display=swap" rel="stylesheet">
<style>
:root{
  --green:#0e5a2c;
  --green-dark:#0a4622;
  --gold:#c6a04a;
  --cream:#fbeab2;
  --cream-soft:#fff6d8;
  --ink:#2a2a2a;
  --muted:#6b6b6b;
  --footer:#1e1e1e;
  --line:#e2e2e2;
}
*{box-sizing:border-box;margin:0;padding:0}
html,body{width:1200px;height:4440px;overflow:hidden}
body{position:relative;background:#fff;font-family:"Barlow",sans-serif;color:var(--ink)}
.abs{position:absolute}
.heading{font-family:"Marcellus",serif;color:var(--green);letter-spacing:2px;text-align:center;font-size:34px;font-weight:400}

/* header */
.site-header{top:0;left:0;width:1200px;height:80px;background:#fff}
.brand{left:108px;top:14px;display:flex;align-items:center;gap:10px;font-family:"Marcellus",serif;font-size:30px;color:var(--green)}
.brand-square{width:28px;height:28px;background:var(--gold)}
.nav{right:120px;top:26px;display:flex;align-items:center;gap:30px;font-size:17px;font-weight:500}
.nav a{color:var(--ink);text-decoration:none}
.nav a.active{color:var(--gold);border-bottom:2px solid var(--gold);padding-bottom:3px}
.btn{display:inline-block;background:var(--green);color:#fff;font-weight:600;font-size:15px;padding:9px 20px;border-radius:3px;text-decoration:none}

/* hero */
.hero{top:80px;left:0;width:1200px;height:612px;background:linear-gradient(160deg,#3d4a37 0%,#6e7a5c 40%,#8b8a72 60%,#4d5743 100%)}
.hero-frame{top:18px;left:22px;width:1156px;height:560px;border:3px solid rgba(255,255,255,.85)}
.hero-text{left:640px;top:200px;color:#fff;font-family:"Marcellus",serif}
.hero-text .welcome{font-size:22px}
.hero-text h1{font-size:64px;font-weight:400;letter-spacing:3px;margin-top:6px}
.hero-text .tag{font-size:32px;letter-spacing:2px;margin-top:2px}
.hero-text .btn{margin-top:26px;font-family:"Barlow",sans-serif}
.dots{left:650px;top:660px;display:flex;gap:8px}
.dots i{width:12px;height:12px;border-radius:50%;background:rgba(255,255,255,.6)}
.dots i:first-child{background:#fff}
.chat{right:18px;top:708px;width:64px;height:64px;border-radius:50%;background:#fff;box-shadow:0 2px 10px rgba(0,0,0,.2);display:flex;align-items:center;justify-content:center}

/* vacancy */
.vacancy{left:222px;top:790px;width:760px;height:320px;background:var(--cream);border:3px solid #fff;outline:1px solid #e8d48f}
.vacancy .heading{margin-top:38px;font-size:32px}
.field-label{font-size:15px;color:#333}
.input{height:36px;background:#fff;border:1px solid #e4e4e4;font-size:13px;color:#aaa;padding:9px 14px}
.select{width:142px;height:36px;background:#fff;border:1px solid #e4e4e4;font-size:13px;color:#999;padding:9px 14px;display:flex;justify-content:space-between}

/* rooms */
.rooms-title{top:1206px;left:0;width:1200px}
.room{top:1300px;width:556px;height:264px;background:#fff;box-shadow:0 2px 14px rgba(0,0,0,.14);display:flex}
.room-photo{width:218px;height:264px;background:linear-gradient(180deg,#2b241c,#6b5a3c 60%,#3a2f22)}
.room-body{padding:22px 20px;flex:1}
.room-body h3{font-family:"Marcellus",serif;font-size:22px;font-weight:400;color:#222}
.room-meta{display:flex;gap:28px;font-size:12px;color:#555;margin-top:10px}
.amen{display:grid;grid-template-columns:1fr 1fr;gap:6px 12px;font-size:12px;color:#444;margin-top:18px}
.amen span::before{content:"✓ ";color:var(--green)}
.view{display:block;margin-top:14px;font-size:13px;font-weight:600;color:var(--green)}
.arrows{top:1622px;left:560px;display:flex;gap:12px}
.arrows i{width:36px;height:36px;border-radius:50%;background:#bbb;display:flex;align-items:center;justify-content:center;color:#fff;font-style:normal}
.arrows i:last-child{background:#d8d8d8}

/* about */
.about{top:1744px;left:0;width:1200px;height:448px;background:var(--green)}
.diamond{left:88px;top:82px;width:282px;height:282px;transform:rotate(45deg);border:4px solid var(--gold);background:linear-gradient(135deg,#8a8a7a,#c9c0a4 50%,#5a5a4c)}
.about-text{left:560px;top:56px;width:580px;color:#fff}
.about-text h2{font-family:"Marcellus",serif;font-weight:400;font-size:32px;color:var(--gold);letter-spacing:2px}
.about-text p{font-size:15px;line-height:1.6;margin-top:16px;color:#e6efe8}
.btn-gold{background:var(--gold);margin-top:26px}

/* badges */
.badges{top:2228px;left:0;width:1200px;height:214px;background:var(--cream)}
.badge{top:58px;width:158px;height:104px;background:#fff;border:2px solid #e6c970}
.badge-arrow{top:92px;width:34px;height:34px;border-radius:50%;background:#999;color:#fff;display:flex;align-items:center;justify-content:center}

/* gallery */
.gallery-title{top:2570px;left:0;width:1200px}
.photo{background:linear-gradient(140deg,#2c2419,#7b6440 55%,#3b2e1f)}

/* testimonials */
.testi-title{top:3282px;left:0;width:1200px}
.testi{top:3350px;left:170px;width:860px;text-align:center}
.testi .label{color:var(--gold);font-weight:600;font-size:15px;letter-spacing:1px}
.testi p{font-size:15px;line-height:1.6;color:#444;margin-top:10px}
.testi .name{margin-top:20px;font-size:17px;font-weight:600}

/* map */
.map{top:3576px;left:0;width:1200px;height:306px;background:radial-gradient(ellipse at 55% 50%,#3a5a6e,#1d3342 60%,#14222c)}
.map-card{left:400px;top:74px;background:#fff;padding:10px 16px;font-size:14px;line-height:1.4;box-shadow:0 2px 8px rgba(0,0,0,.3)}
.pin{left:586px;top:140px}

/* footer */
.footer{top:3882px;left:0;width:1200px;height:558px;background:var(--footer);color:#fff}
.footer-brand{top:62px;display:flex;align-items:center;gap:10px;font-family:"Marcellus",serif;font-size:30px;color:var(--gold)}
.footer-brand.alt{color:#b9a06a}
.footer-nav{top:196px;left:0;width:1200px;display:flex;justify-content:center;gap:44px;font-size:17px}
.contact{top:262px;width:260px;text-align:center}
.ic{width:56px;height:56px;border-radius:50%;background:var(--gold);margin:0 auto;display:flex;align-items:center;justify-content:center}
.contact h4{font-weight:500;font-size:15px;margin-top:14px;letter-spacing:1px}
.contact p{font-size:14px;color:#cfcfcf;margin-top:4px}
.footer-bottom{top:508px;left:110px;width:980px;border-top:1px solid #3a3a3a;padding-top:12px;display:flex;justify-content:space-between;font-size:13px;color:#bbb}
.social{display:flex;gap:14px}
.social i{width:16px;height:16px;border-radius:50%;background:#bbb;display:block}
</style>
</head>
<body>

<header class="site-header abs">
  <div class="brand abs"><span class="brand-square"></span>Corvena Hotel</div>
  <nav class="nav abs">
    <a class="active" href="#">Home</a><a href="#">About</a><a href="#">Rooms</a><a href="#">Gallery</a><a href="#">Contact</a>
    <a class="btn" href="#">Book Now</a>
  </nav>
</header>

<section class="hero abs" role="img" aria-label="Photo of the hotel terrace with wooden decking and greenery">
  <div class="hero-frame abs"></div>
  <div class="hero-text abs">
    <div class="welcome">Welcome To</div>
    <h1>CORVENA HOTEL</h1>
    <div class="tag">ENJOY A LUXURY EXPERIENCE</div>
    <a class="btn" href="#">Explore</a>
  </div>
  <div class="dots abs" style="top:580px"><i></i><i></i><i></i><i></i></div>
</section>

<div class="chat abs">
  <svg width="34" height="30" viewBox="0 0 34 30"><rect x="1" y="1" width="32" height="22" rx="4" fill="#7a8a2c"/><path d="M8 23 L6 29 L14 23Z" fill="#7a8a2c"/><rect x="8" y="9" width="18" height="3" fill="#fff"/><rect x="8" y="14" width="12" height="3" fill="#fff"/></svg>
</div>

<section class="vacancy abs">
  <h2 class="heading">CHECK VACANCY</h2>
  <div class="abs" style="left:92px;top:92px">
    <div class="field-label">Full Name</div>
    <div class="input" style="width:330px;margin-top:8px">Alex Carter</div>
  </div>
  <div class="abs" style="left:438px;top:92px">
    <div class="field-label">Email ID</div>
    <div class="input" style="width:232px;margin-top:8px">name@example.com</div>
  </div>
  <div class="abs" style="left:92px;top:178px">
    <div class="field-label">Rooms</div>
    <div class="select" style="margin-top:8px"><span>Select</span><span>▾</span></div>
  </div>
  <div class="abs" style="left:264px;top:178px">
    <div class="field-label">Adults</div>
    <div class="select" style="margin-top:8px"><span>Select</span><span>▾</span></div>
  </div>
  <div class="abs" style="left:436px;top:178px">
    <div class="field-label">Children</div>
    <div class="select" style="margin-top:8px"><span>Select</span><span>▾</span></div>
  </div>
  <a class="btn abs" href="#" style="left:596px;top:208px;padding:9px 24px">Submit</a>
</section>

<h2 class="heading rooms-title abs">ROOMS</h2>

<article class="room abs" style="left:-216px">
  <div class="room-body">
    <h3>TRIPLE ROOM</h3>
    <div class="room-meta"><span>3 single beds</span><span>Room size: 28 m2</span></div>
    <div class="amen"><span>Flat screen Tv</span><span>Air Conditioner</span><span>Mini Bar</span><span>Non Smoking</span><span>Safebox</span><span>Free Wifi</span><span>Alarm Clock Service</span></div>
    <a class="view" href="#">View More</a>
  </div>
</article>
<article class="room abs" style="left:330px">
  <div class="room-photo" role="img" aria-label="Photo of a single room with bed and wall art"></div>
  <div class="room-body">
    <h3>SINGLE ROOM</h3>
    <div class="room-meta"><span>1 single bed</span><span>Room size: 16 m2</span></div>
    <div class="amen"><span>Flat screen Tv</span><span>Air Conditioner</span><span>Mini Bar</span><span>Non Smoking</span><span>Safebox</span><span>Free Wifi</span><span>Alarm Clock Service</span></div>
    <a class="view" href="#">View More</a>
  </div>
</article>
<article class="room abs" style="left:880px">
  <div class="room-photo" role="img" aria-label="Photo of a double room with bed and lamps"></div>
  <div class="room-body">
    <h3>DOUBLE ROOM</h3>
    <div class="room-meta"><span>1 double bed</span><span>Room size: 22 m2</span></div>
    <div class="amen"><span>Flat screen Tv</span><span>Air Conditioner</span><span>Mini Bar</span><span>Non Smoking</span><span>Safebox</span><span>Free Wifi</span><span>Alarm Clock Service</span></div>
    <a class="view" href="#">View More</a>
  </div>
</article>
<div class="room-photo abs" style="top:1300px;left:120px;width:218px" role="img" aria-label="Photo of a triple room"></div>

<div class="arrows abs"><i>‹</i><i>›</i></div>

<section class="about abs">
  <div class="diamond abs" role="img" aria-label="Photo of the rooftop terrace with white canopy"></div>
  <div class="about-text abs">
    <h2>ABOUT US</h2>
    <p>Situated at the very heart of Rhodes town, the hotel provides easy access to all major points of interest at walking distance.</p>
    <p>The hotel is renowned in the local market due to its operation which runs 365 days a year. All rooms have been renovated recently and offer a unique design with modern furnishes. Being in constant operation for the last 47 years, and gone through numerous renovations the hotel operates mainly with travellers who value and appreciate its comfort, cleanliness, family attitude, amenities and personality just to name a few.</p>
    <a class="btn btn-gold" href="#">Learn More</a>
  </div>
</section>

<section class="badges abs">
  <div class="badge-arrow abs" style="left:96px">‹</div>
  <div class="badge abs" style="left:188px" role="img" aria-label="Travel award badge"></div>
  <div class="badge abs" style="left:402px" role="img" aria-label="Travel award badge"></div>
  <div class="badge abs" style="left:616px" role="img" aria-label="Travel award badge"></div>
  <div class="badge abs" style="left:830px" role="img" aria-label="Travellers choice badge"></div>
  <div class="badge-arrow abs" style="left:1070px">›</div>
</section>

<h2 class="heading gallery-title abs">GALLERY</h2>
<div class="photo abs" style="left:110px;top:2680px;width:316px;height:244px" role="img" aria-label="Photo of a guest room"></div>
<div class="photo abs" style="left:436px;top:2680px;width:280px;height:244px" role="img" aria-label="Photo of the lounge"></div>
<div class="photo abs" style="left:768px;top:2680px;width:318px;height:244px" role="img" aria-label="Photo of a room with warm lighting"></div>
<div class="photo abs" style="left:110px;top:2934px;width:648px;height:236px" role="img" aria-label="Photo of the hotel dining area"></div>
<div class="photo abs" style="left:768px;top:2934px;width:318px;height:236px" role="img" aria-label="Photo of the reception"></div>

<h2 class="heading testi-title abs">TESTIMONIALS</h2>
<div class="testi abs">
  <div class="label">PERFECT SPOT!</div>
  <p>Situated between old town and new town, the hotel offers all you can ask for. There are many shops around, walking distance to old town, where there are many restaurants and tourist attractions. The hotel is very clean, and the staff is extremely friendly and helpful. They were very easy with the reservation and were willing to help you with smiles all the time. Open buffet breakfast is excellent: you can find almost everything you want to eat. The hotel definitely made my stay in Rhodes an unforgettable experience.</p>
  <div class="name">Mara K</div>
</div>

<section class="map abs" role="img" aria-label="Satellite map of Rhodes town showing the hotel location">
  <div class="map-card abs">14 Orchid Str,<br>Rhodes 851 00</div>
  <svg class="pin abs" width="26" height="36" viewBox="0 0 26 36"><path d="M13 0C6 0 0 6 0 13c0 9 13 23 13 23s13-14 13-23C26 6 20 0 13 0z" fill="#e23b2e"/><circle cx="13" cy="13" r="5" fill="#fff"/></svg>
</section>

<footer class="footer abs">
  <div class="footer-brand abs" style="left:300px"><span class="brand-square"></span>Corvena Hotel</div>
  <div class="footer-brand alt abs" style="left:700px">Alvena Luxury Class</div>
  <nav class="footer-nav abs"><span>Home</span><span>About</span><span>Rooms</span><span>Gallery</span><span>Contact</span></nav>
  <div class="contact abs" style="left:66px">
    <div class="ic"><svg width="24" height="24" viewBox="0 0 24 24"><path d="M6 2l4 4-2 3c1 3 4 6 7 7l3-2 4 4-3 4C10 22 2 14 2 5z" fill="#fff"/></svg></div>
    <h4>PHONE</h4><p>+30 22410 55100</p>
  </div>
  <div class="contact abs" style="left:470px">
    <div class="ic"><svg width="22" height="28" viewBox="0 0 26 36"><path d="M13 0C6 0 0 6 0 13c0 9 13 23 13 23s13-14 13-23C26 6 20 0 13 0z" fill="#fff"/><circle cx="13" cy="13" r="5" fill="#c6a04a"/></svg></div>
    <h4>ADDRESS</h4><p>14 Orchid Str, Rhodes 851 00</p>
  </div>
  <div class="contact abs" style="left:874px">
    <div class="ic"><svg width="26" height="20" viewBox="0 0 26 20"><rect x="1" y="1" width="24" height="18" fill="none" stroke="#fff" stroke-width="2"/><path d="M1 1l12 10L25 1" fill="none" stroke="#fff" stroke-width="2"/></svg></div>
    <h4>EMAIL</h4><p>info@corvenahotel.gr</p>
  </div>
  <div class="footer-bottom abs"><span>2023 Corvena Hotel All Rights Reserved.</span><span class="social"><i></i><i></i></span></div>
</footer>

</body>
</html>
```